Flyer für Backwarenlieferservice
Liebe Designer,
wir sind begeistert, dass du die Möglichkeit hast, das Design für unseren Werbeflyer zu gestalten. Unser Backwarenlieferservice, die 'Teigwichtelhof', legt großen Wert auf eine kreative und ansprechende Gestaltung, die unsere Probessendung in den Mittelpunkt stellt. Bitte beachte die folgenden Informationen bei der Entwicklung deines Designs:
WICHTIG FÜR UNS: Das unser Maskottchen eingebunden ist und das wir mit dem Flyer für unsere kostenlose Probesendung in den Fokus stellen wollen. Ein altes Design ist im Anhang, der Text sollte nicht identisch sein, aber in die Richtung gehen.
Aufgabenstellung
1. Was ist uns besonders wichtig im Design?
Einladende Optik: Das Design sollte fröhlich und einladend wirken, um die Freude an köstlichen Backwaren zu betonen.
Fokussierung auf die Probessendung: Betone die Möglichkeit, unsere Backwaren einmalig kostenlos auszuprobieren. Dies sollte klar und auffällig im Design integriert sein.
Kinderfreundlichkeit: Da junge Familien eine wichtige Zielgruppe sind, ist ein kinderfreundliches Design mit ansprechenden Illustrationen oder Bildern von Backwaren für Kinder wünschenswert.
Klare und prägnante Botschaft: Die Botschaft sollte leicht verständlich und einprägsam sein, damit potenzielle Kunden sofort die Vorteile unserer Probessendung erkennen.
2. Was macht unsere Firma aus?
Probessendung: Unser Alleinstellungsmerkmal ist die kostenlose Probessendung, die es neuen Kunden ermöglicht, unsere Backwaren unverbindlich zu testen.
Qualität und Vielfalt: Betone die Qualität und Vielfalt unserer Backwaren. Bilder von handwerklich hergestellten, knusprigen Produkten können dabei hilfreich sein.
Familienfreundlichkeit: Wir sind darauf ausgerichtet, auch den Bedürfnissen von jungen Familien gerecht zu werden. Dies spiegelt sich in unserem Sortiment und unseren Angeboten wider.
3. Wer ist unsere Zielgruppe?
Junge Familien mit Kindern: Eltern, die nach hochwertigen Backwaren suchen und Wert auf eine kostenlose Probessendung legen, um unser Sortiment kennenzulernen.
Alle Personen ab ca. 25 Jahren: Auch Einzelpersonen und Paare ab 25 Jahren, die auf der Suche nach qualitativ hochwertigen und abwechslungsreichen Backwaren sind.
Designelemente:
Schriften: Nutze die Schriften 'Audiowide' und 'Alike' für einen einheitlichen Markenauftritt.
Farben: Unsere Hauptfarben sind Grau und Orange. Bitte integriere diese Farben harmonisch in das Design.
Format: Der Flyer hat das A5-Format, aber auch andere Formate können in Betracht gezogen werden.
Vielen Dank für deine Kreati..

```html
<!DOCTYPE html>
<html lang="de">
<head>
<meta charset="utf-8">
<title>Teigwichtelhof – Flyer Probesendung</title>
<link href="https://fonts.googleapis.com/css2?family=Alike&family=Audiowide&display=swap" rel="stylesheet">
<style>
:root{
  --stage:#000000;
  --paper:#fbfbfb;
  --graphite:#4a4a4a;
  --orange:#f3951e;
  --orange-deep:#e8871a;
  --white:#ffffff;
}
*{margin:0;padding:0;box-sizing:border-box}
html,body{width:1200px;height:849px;overflow:hidden;background:var(--stage)}
.stage{position:relative;width:1200px;height:849px}
.flyer{position:absolute;top:75px;width:501px;height:711px;background:var(--paper);overflow:hidden}
.flyer--delivery{left:61px}
.flyer--sample{left:643px}
.band{position:absolute;left:0;width:100%}
.band--dark{background:var(--graphite)}
.band--orange{background:var(--orange)}
.brand-name{position:absolute;left:116px;font-family:"Audiowide",sans-serif;font-size:19px;letter-spacing:11.6px;color:var(--orange);white-space:nowrap}
.tagline{position:absolute;left:114px;font-family:"Audiowide",sans-serif;font-size:12.2px;color:var(--orange);white-space:nowrap;letter-spacing:.1px}
.mascot{position:absolute;left:8px;width:108px;height:174px;border-radius:40px 40px 24px 24px;background:linear-gradient(180deg,#e9a24a 0%,#f2f2f2 45%,#8a8a8a 85%,#7a5030 100%)}
.photo{position:absolute;left:0;width:100%}
.photo--breads-light{top:248px;height:332px;background:linear-gradient(180deg,#a9a9ae 0%,#cfcfd2 35%,#b07a44 60%,#8c5a2e 80%,#d8d4cf 100%)}
.photo--breads-wood{top:246px;height:207px;background:linear-gradient(180deg,#8a6240 0%,#b48a5e 35%,#7a6250 70%,#5d4c40 100%)}
.headline{position:absolute;font-family:"Audiowide",sans-serif;line-height:1}
.headline--bed{left:26px;top:268px;font-size:41px;color:var(--orange)}
.headline--bed span{display:block}
.headline--bed .line2{margin-left:13px;margin-top:2px}
.headline--bed sup{font-size:9px;vertical-align:top;margin-left:-4px}
.headline--sample{left:25px;top:347px;font-size:41px;color:var(--white)}
.headline--sample span{display:block;margin-bottom:3px}
.heart{position:absolute;width:72px;height:68px}
.section-title{position:absolute;font-family:"Audiowide",sans-serif;color:var(--orange)}
.section-title--service{left:21px;top:605px;font-size:20px}
.section-title--try{left:25px;top:555px;font-size:15.5px}
.copy{position:absolute;font-family:"Alike",serif;color:var(--orange);line-height:19px}
.copy--service{left:21px;top:629px;font-size:12.2px;line-height:17.5px}
.copy--intro{left:25px;top:474px;width:470px;font-size:12.3px}
.copy--contact{left:25px;top:572px;width:470px;font-size:12.3px}
.footnote{position:absolute;right:10px;top:684px;font-family:"Alike",serif;font-size:5.5px;color:var(--orange)}
.imprint{position:absolute;left:371px;top:637px;font-family:"Alike",serif;font-size:8px;line-height:8.4px;color:var(--orange)}
.imprint p+p{margin-top:8px}
</style>
</head>
<body>
<div class="stage">

  <!-- Flyer: Lieferservice -->
  <section class="flyer flyer--delivery">
    <div class="band band--dark" style="top:39px;height:101px"></div>
    <div class="band band--dark" style="top:160px;height:19px"></div>
    <div class="brand-name" style="top:76px">TEIGWICHTELHOF</div>
    <div class="tagline" style="top:162px">duftend, knusprig, kernig, gesund, lecker, ofenfrisch</div>
    <div class="mascot" role="img" aria-label="Maskottchen: Bäcker mit Schürze, Brotkorb und Daumen hoch" style="top:46px"></div>

    <div class="band band--orange" style="top:238px;height:10px"></div>
    <div class="photo photo--breads-light" role="img" aria-label="Foto: verschiedene Brote und Brötchen auf einem Holzbrett mit Leinentuch"></div>
    <div class="band band--orange" style="top:580px;height:10px"></div>

    <h1 class="headline headline--bed"><span>„Frühstück direkt</span><span class="line2">ans Bett<sup>*</sup>“</span></h1>

    <svg class="heart" style="left:377px;top:552px" viewBox="0 0 72 68" aria-label="jetzt Gratis testen">
      <g transform="rotate(18 36 34)">
        <path d="M36 64 C18 50 4 38 6 22 C8 10 22 4 32 14 L36 18 L40 14 C50 4 64 10 66 22 C68 38 54 50 36 64 Z" fill="var(--orange)"/>
        <text x="37" y="24" text-anchor="middle" font-family="Audiowide, sans-serif" font-size="9" fill="#fff">jetzt</text>
        <text x="36" y="35" text-anchor="middle" font-family="Audiowide, sans-serif" font-size="9" fill="#fff">Gratis</text>
        <text x="36" y="46" text-anchor="middle" font-family="Audiowide, sans-serif" font-size="9" fill="#fff">testen</text>
      </g>
    </svg>

    <h2 class="section-title section-title--service">Backwaren Lieferservice</h2>
    <p class="copy copy--service">Werktags bis 7:00 am Wochenende bis 8:30<br>Keine Mindestbestellmenge</p>

    <div class="band band--dark" style="top:681px;height:15px"></div>
    <div class="footnote">* an die Haustür</div>
  </section>

  <!-- Flyer: Probesendung -->
  <section class="flyer flyer--sample">
    <div class="band band--dark" style="top:37px;height:101px"></div>
    <div class="band band--dark" style="top:157px;height:19px"></div>
    <div class="brand-name" style="top:74px">TEIGWICHTELHOF</div>
    <div class="tagline" style="top:159px">duftend, knusprig, kernig, gesund, lecker, ofenfrisch</div>
    <div class="mascot" role="img" aria-label="Maskottchen: Bäcker mit Schürze, Brotkorb und Daumen hoch" style="top:42px"></div>

    <div class="band band--orange" style="top:236px;height:10px"></div>
    <div class="photo photo--breads-wood" role="img" aria-label="Foto: Körnerbrötchen, Croissants, Brezeln und Getreide auf rustikalem Holztisch"></div>
    <div class="band band--orange" style="top:453px;height:10px"></div>

    <svg class="heart" style="left:377px;top:210px" viewBox="0 0 72 68" aria-label="jetzt Gratis testen">
      <g transform="rotate(18 36 34)">
        <path d="M36 64 C18 50 4 38 6 22 C8 10 22 4 32 14 L36 18 L40 14 C50 4 64 10 66 22 C68 38 54 50 36 64 Z" fill="var(--orange)"/>
        <text x="37" y="24" text-anchor="middle" font-family="Audiowide, sans-serif" font-size="9" fill="#fff">jetzt</text>
        <text x="36" y="35" text-anchor="middle" font-family="Audiowide, sans-serif" font-size="9" fill="#fff">Gratis</text>
        <text x="36" y="46" text-anchor="middle" font-family="Audiowide, sans-serif" font-size="9" fill="#fff">testen</text>
      </g>
    </svg>

    <h1 class="headline headline--sample"><span>kostenlose</span><span>Probesendung</span></h1>

    <p class="copy copy--intro">Gemeinsam mit unseren Partnerbäckereien arbeiten wir Hand in Hand an der Zufriedenheit unserer Kunden und liefern unsere Vielfalt direkt an die Haustür. Die von uns angebotenen Waren werden mit ausgewählten Zutaten nach guter alter Handwerkstradition gebacken.</p>
    <h2 class="section-title section-title--try">Probier´s aus</h2>
    <p class="copy copy--contact">ruf uns an unter 04203-5519370 zwischen 09 – 12 Uhr und 14 – 16 Uhr oder ganz bequem unter www.teigwichtelhof.de</p>

    <footer class="band band--dark" style="top:624px;height:73px"></footer>
    <address class="imprint" style="font-style:normal">
      <p>Teigwichtelhof<br>Lindenkampstraße 14<br>28195 Bremen</p>
      <p>www.teigwichtelhof.de<br>kunden@teigwichtelhof.de</p>
    </address>
  </section>

</div>
</body>
</html>
```